Business Recognition Design

We need a design for a recognition to be given to business leaders in our community.
The recognition shall be made on a brass plaque on wood panel background (picture attached, please use it as a background), and all drawing must be in vectors and only one color (black).
It should also have a logo on the top and signature on the right bottom.
The text is enclosed in DOC file.
Updates

Reason: just to be able to find the best solution

Reason: None of the suggestion is good enough. Logo in general is too big in comparison with the rest of the plate.

Industry/Entity Type

Business

Requirements
Must have
• - standard Windows font (or possibility to install the same font on Windows), as the name on the recognition shall be printed in the same font
Nice to have
• - some graphic element (in curves) representing achievements in business
- should look great :)

```html
<!DOCTYPE html>
<html lang="de">
<head>
<meta charset="utf-8">
<title>Auszeichnung – Unternehmerplakette</title>
<link rel="stylesheet" href="https://fonts.googleapis.com/css2?family=Arimo:wght@400;700&display=swap">
<style>
  :root {
    --backdrop: #3c3c3c;
    --wood-light: #7a5538;
    --wood-dark: #4b2f1d;
    --wood-edge: #3a2314;
    --brass-deep: #b8902c;
    --brass-mid: #d8b44c;
    --brass-bright: #f2d77c;
    --engrave: #1f160c;
    --screw-light: #f6e3a0;
    --screw-dark: #8a6a1c;
  }
  html, body {
    margin: 0;
    padding: 0;
    width: 1200px;
    height: 832px;
    overflow: hidden;
    background: var(--backdrop);
  }
  .canvas {
    position: relative;
    width: 1200px;
    height: 832px;
    font-family: "Arimo", Arial, sans-serif;
    color: var(--engrave);
  }
  .wood-panel {
    position: absolute;
    left: 160px;
    top: 66px;
    width: 878px;
    height: 690px;
    box-sizing: border-box;
    border: 4px solid var(--wood-edge);
    background: linear-gradient(100deg, var(--wood-dark), var(--wood-light) 45%, var(--wood-dark));
  }
  .brass-plate {
    position: absolute;
    left: 190px;
    top: 94px;
    width: 818px;
    height: 629px;
    background: linear-gradient(160deg, var(--brass-deep) 0%, var(--brass-bright) 30%, var(--brass-mid) 60%, var(--brass-deep) 100%);
  }
  .plate-art {
    position: absolute;
    left: 0;
    top: 0;
    width: 1200px;
    height: 832px;
  }
  .frame-outer { fill: none; stroke: var(--engrave); stroke-width: 4; }
  .frame-inner { fill: none; stroke: var(--engrave); stroke-width: 2.5; }
  .ornament { fill: var(--engrave); opacity: 0.85; }
  .screw { fill: url(#screwShade); stroke: var(--screw-dark); stroke-width: 1; }

  .line {
    position: absolute;
    left: 0;
    width: 1200px;
    margin: 0;
    text-align: center;
    line-height: 1;
  }
  .brand-name { top: 278px; font-size: 30px; font-weight: 700; letter-spacing: -0.5px; }
  .award-title { top: 320px; font-size: 50px; font-weight: 400; letter-spacing: 1px; }
  .award-subtitle { top: 382px; font-size: 27px; font-weight: 700; }
  .award-year { top: 420px; font-size: 27px; font-weight: 700; }
  .award-for { top: 453px; font-size: 17px; }
  .recipient { top: 476px; font-size: 24px; font-weight: 700; }
  .citation { font-size: 17px; }
  .citation-1 { top: 507px; }
  .citation-2 { top: 531px; }
  .citation-3 { top: 556px; }
  .citation strong { font-size: 19px; }
  .citation small { font-size: 11px; font-weight: 700; }
  .signoff {
    position: absolute;
    top: 652px;
    font-size: 18px;
    line-height: 1;
    margin: 0;
  }
  .signoff-place { left: 380px; }
  .signoff-signer { left: 670px; }
</style>
</head>
<body>
<main class="canvas">
  <div class="wood-panel"></div>
  <div class="brass-plate"></div>

  <svg class="plate-art" viewBox="0 0 1200 832" aria-hidden="false">
    <defs>
      <radialGradient id="screwShade" cx="40%" cy="35%" r="65%">
        <stop offset="0%" stop-color="var(--screw-light)"/>
        <stop offset="100%" stop-color="var(--screw-dark)"/>
      </radialGradient>
    </defs>
    <!-- engraved frame with scooped corners -->
    <path class="frame-outer" d="M255,200 H945 A30,30 0 0 0 975,230 V662 A30,30 0 0 0 945,692 H255 A30,30 0 0 0 225,662 V230 A30,30 0 0 0 255,200 Z"/>
    <path class="frame-inner" d="M259,212 H941 A18,18 0 0 0 959,230 V662 A18,18 0 0 0 941,680 H259 A18,18 0 0 0 241,662 V230 A18,18 0 0 0 259,212 Z"/>
    <!-- top flourish area -->
    <rect class="ornament" x="512" y="156" width="176" height="72" rx="30" role="img" aria-label="Verschnörkeltes Zierornament über dem Rahmen"/>
    <!-- mounting screws -->
    <circle class="screw" cx="228" cy="132" r="9"/>
    <circle class="screw" cx="970" cy="132" r="9"/>
    <circle class="screw" cx="228" cy="686" r="9"/>
    <circle class="screw" cx="970" cy="686" r="9"/>
  </svg>

  <p class="line brand-name">Kapitalwerk</p>
  <h1 class="line award-title">AUSZEICHNUNG</h1>
  <p class="line award-subtitle">als herausragendster Unternehmer</p>
  <p class="line award-year">Deutschlands 2013</p>
  <p class="line award-for">für</p>
  <p class="line recipient">Herrn Dipl.-Kfm. Max Muster</p>
  <p class="line citation citation-1">Unter der Leitung von <strong>Herr Dipl.-Kfm.</strong> <small>Max Muster</small></p>
  <p class="line citation citation-2">hat sich die FIRMA GmbH im Jahr 2013 unter den ersten 5% der</p>
  <p class="line citation citation-3">größten deutschen Wirtschaftsunternehmen platziert.</p>

  <p class="signoff signoff-place">Gilching, 20. Juni 2013</p>
  <p class="signoff signoff-signer">Helena Brandt</p>
</main>
</body>
</html>
```